professional business card design

Business card design. Photos have been uploaded and i am open to the designer choosing which photos to use. Would like the card to be mostyly in a grey scale design with black, whites, silver & grey colours. I have added copy of our flyer as would like on the back side of card our services to be listed. Do not use any bright colurs such as blue red green or yellow. i need to be able to edit the phone number and naem in the final card design submitted.

Target Market(s)

Clients

Industry/Entity Type

earhmovibng and transport

Contact Information for Business Card

Director Name, address, email, phone number and services

Colors

Designer to choose only greyscale colors for use in the design.

Requirements
Should not have
• no yellow, red, blue or green

```html
<!DOCTYPE html>
<html lang="en">
<head>
<meta charset="utf-8">
<title>Haulcrest Business Card</title>
<link rel="stylesheet" href="https://fonts.googleapis.com/css2?family=Oswald:wght@500&family=Open+Sans:wght@400;700&family=Michroma&display=swap">
<style>
  :root{
    --page:#2b2b2b;
    --card:#050505;
    --pattern-hi:#3a3a3a;
    --pattern-lo:#0c0c0c;
    --silver:#c9c9c9;
    --white:#ffffff;
    --grey:#8a8a8a;
  }
  *{margin:0;padding:0;box-sizing:border-box}
  html,body{width:1200px;height:1198px;overflow:hidden;background:var(--page)}
  .card{position:absolute;left:100px;width:1000px;height:560px;border-radius:18px;background:var(--card);overflow:hidden;box-shadow:0 10px 30px rgba(0,0,0,.5)}
  .card--front{top:20px}
  .card--back{top:618px}
  .texture{position:absolute;left:0;top:0;width:100%}
  .card--front .texture{height:355px;background:radial-gradient(ellipse at 50% 30%,var(--pattern-hi),var(--pattern-lo) 75%)}
  .card--back .texture{height:340px;background:linear-gradient(180deg,var(--pattern-hi),var(--pattern-lo))}
  .brand{position:absolute;font-family:"Open Sans",sans-serif;font-weight:700;color:var(--silver)}
  .card--front .brand{left:0;right:0;top:130px;text-align:center;font-size:64px;letter-spacing:2px}
  .card--back .brand{left:60px;top:48px;font-size:38px}
  .services{position:absolute;left:50px;top:370px;right:40px;color:var(--white)}
  .services__title{font-family:"Michroma",sans-serif;font-size:26px;letter-spacing:2px;margin-bottom:22px}
  .services__list{display:grid;grid-template-columns:352px 352px 1fr;grid-auto-flow:column;grid-template-rows:repeat(5,21px);list-style:none;font-family:"Michroma",sans-serif;font-size:11px;font-variant:small-caps;letter-spacing:.5px}
  .services__list li::before{content:"\25AF  ";}
  .services__list .col2{grid-column:2}
  .services__list .col3{grid-column:3}
  .truck{position:absolute;left:505px;top:70px;width:470px;height:270px;background:linear-gradient(160deg,#bdbdbd,#5a5a5a 55%,#1a1a1a);border-radius:6px}
  .person{position:absolute;left:50px;top:228px;color:var(--white)}
  .person__name{font-family:"Oswald",sans-serif;font-weight:500;font-size:52px;line-height:1}
  .person__role{font-family:"Open Sans",sans-serif;font-size:26px;margin-top:4px}
  .rule{position:absolute;background:var(--white)}
  .rule--short{left:52px;top:345px;width:222px;height:3px}
  .rule--long{left:52px;top:357px;width:900px;height:3px}
  .contact{position:absolute;top:385px;color:var(--white);font-family:"Open Sans",sans-serif;font-size:26px;line-height:33px}
  .contact svg{display:block;width:48px;height:48px;margin-bottom:26px}
  .contact--phone{left:45px}
  .contact--web{left:270px}
  .contact--address{left:618px}
</style>
</head>
<body>
  <section class="card card--front">
    <div class="texture" role="img" aria-label="Dark perforated metal hex texture"></div>
    <div class="brand">Haulcrest Pty Ltd</div>
    <div class="services">
      <h2 class="services__title">OUR SERVICES</h2>
      <ul class="services__list">
        <li>Over size loads/ Hot Shot Loads</li>
        <li>Potable Water Deliveries</li>
        <li>Sand &amp; Metal Supply &amp; Cartage:</li>
        <li>Raad Train Tankers</li>
        <li>Mine Site accredited equipment &amp; Operators</li>
        <li class="col2">Heavy Vehicle Recovery Services</li>
        <li class="col2">Road Building / Maintenance</li>
        <li class="col2">Raad Train Tippers</li>
        <li class="col2">Road Train Flat Tops</li>
        <li class="col3">Raad Train Tippers</li>
        <li class="col3">Earthworks</li>
        <li class="col3">Drop Deck Trailers</li>
      </ul>
    </div>
  </section>

  <section class="card card--back">
    <div class="texture" role="img" aria-label="Dark perforated metal hex texture"></div>
    <div class="brand">Haulcrest</div>
    <div class="truck" role="img" aria-label="Greyscale photo of a prime mover hauling earthmoving machinery on a low loader"></div>
    <div class="person">
      <div class="person__name">Your Name Here</div>
      <div class="person__role">Graphic Designer</div>
    </div>
    <div class="rule rule--short"></div>
    <div class="rule rule--long"></div>
    <div class="contact contact--phone">
      <svg viewBox="0 0 48 48" fill="none" stroke="#fff" stroke-width="2.2" stroke-linecap="round" stroke-linejoin="round"><path d="M10 6l7 1 3 9-4 3c2 5 6 9 11 11l3-4 9 3 1 7c-1 3-4 5-7 4C20 38 10 28 7 14c-1-3 1-7 3-8z"/><path d="M28 10a10 10 0 0 1 10 10M28 4a16 16 0 0 1 16 16"/></svg>
      +1 2345 6789<br>+1 2345 6789
    </div>
    <div class="contact contact--web">
      <svg viewBox="0 0 48 48" fill="none" stroke="#fff" stroke-width="2.2"><circle cx="24" cy="24" r="19"/><path d="M5 24h38M24 5c-7 6-7 32 0 38M24 5c7 6 7 32 0 38M9 13h30M9 35h30"/></svg>
      your email goes here<br>your website name here
    </div>
    <div class="contact contact--address">
      <svg viewBox="0 0 48 48" fill="none" stroke="#fff" stroke-width="2.2" stroke-linejoin="round"><path d="M5 24L24 6l19 18M10 20v22h28V20"/><rect x="19" y="30" width="10" height="12"/><rect x="21" y="17" width="6" height="6"/></svg>
      123 Anywhere Street, City,<br>Country Code-12345
    </div>
  </section>
</body>
</html>
```